Marlowe Crest Realty business card design

Looking for an upscale and clean business card design and updated logo. I sell to a very high-end south Florida real estate market.
Target Market(s)
High-end real estate in south Florida real estate market
Industry/Entity Type
Real Estate Agent
Contact Information for Business Card
Marlowe Crest Realty, Inc
738 West Pinecrest Ave, Suite 410/510, Fort Lauderdale, FL 33308
Gary Whitlock - Broker/Owner
954-327-8846 Direct
garyshomes@quellmail.com
Website: DwellTarrowBay.com
Font styles to use
Other font styles liked:
- Copperplate Gothic, Georgia, etc.
Requirements
Must have
- My photo, company name, my name and title, all info stated in Details above
Nice to have
- Luxury home design element, waterfront

```html
<!DOCTYPE html>
<html lang="en">
<head>
<meta charset="utf-8">
<title>Marlowe Crest Realty – Business Card</title>
<link rel="stylesheet" href="https://fonts.googleapis.com/css2?family=Gelasio&family=Marcellus+SC&display=swap">
<style>
  :root {
    --backdrop: #e3e3e3;
    --card-white: #ffffff;
    --sun-gold: #f4b92a;
    --gold-band-start: #f2b01e;
    --gold-band-end: #f7cc3f;
    --ink: #1e1e1e;
    --divider: #2a2a2a;
    --card-dark-top: #333333;
    --card-dark-bottom: #1f1f1f;
    --silver: #d9d9d9;
    --photo-top: #5a6f9c;
    --photo-bottom: #1f3a86;
  }
  html, body {
    margin: 0;
    padding: 0;
    width: 1200px;
    height: 1200px;
    overflow: hidden;
    background: var(--backdrop);
  }
  .canvas {
    position: relative;
    width: 1200px;
    height: 1200px;
  }
  .card {
    position: absolute;
    left: 120px;
    width: 960px;
    height: 547px;
    border-radius: 26px;
    overflow: hidden;
    box-shadow: 0 12px 24px rgba(0,0,0,0.18);
  }
  .card-front { top: 28px; background: var(--card-white); }
  .card-back {
    top: 625px;
    background: linear-gradient(180deg, var(--card-dark-top), var(--card-dark-bottom));
  }
  .gold-band {
    position: absolute;
    left: 0; right: 0; bottom: 0;
    height: 17px;
    background: linear-gradient(90deg, var(--gold-band-start), var(--gold-band-end));
  }
  .brand {
    position: absolute;
    display: flex;
    align-items: center;
    gap: 22px;
  }
  .brand-front { left: 80px; top: 221px; }
  .brand-back { left: 66px; top: 228px; }
  .brand-dot {
    width: 90px; height: 90px;
    border-radius: 50%;
    flex: none;
  }
  .brand-front .brand-dot { background: var(--sun-gold); }
  .brand-back .brand-dot { background: var(--silver); }
  .brand-name {
    font-family: "Gelasio", Georgia, serif;
    font-size: 24px;
    white-space: nowrap;
  }
  .brand-front .brand-name { color: var(--ink); }
  .brand-back .brand-name { color: var(--silver); font-size: 27px; }
  .divider {
    position: absolute;
    left: 504px; top: 152px;
    width: 1.5px; height: 230px;
    background: var(--divider);
  }
  .contact {
    position: absolute;
    left: 544px; top: 142px;
    font-family: "Marcellus SC", "Copperplate", serif;
    color: var(--ink);
  }
  .agent-name {
    margin: 0;
    font-size: 33px;
    letter-spacing: 1px;
    color: var(--sun-gold);
    line-height: 1.1;
  }
  .agent-title { margin: 2px 0 18px; font-size: 20px; letter-spacing: 1px; }
  .address { margin: 0 0 16px; font-size: 18.5px; letter-spacing: 1.2px; line-height: 24px; }
  .reach { list-style: none; margin: 0; padding: 0; font-size: 18px; letter-spacing: 1px; }
  .reach li { display: flex; align-items: center; gap: 12px; height: 25px; }
  .reach svg { width: 16px; height: 16px; flex: none; }
  .portrait {
    position: absolute;
    right: 0; top: 0;
    width: 348px; height: 547px;
    background: linear-gradient(180deg, var(--photo-top) 0%, var(--photo-bottom) 45%, #1a3278 100%);
  }
</style>
</head>
<body>
<main class="canvas">
  <section class="card card-front" aria-label="Card front">
    <div class="brand brand-front">
      <span class="brand-dot"></span>
      <span class="brand-name">Marlowe Crest Realty, Inc.</span>
    </div>
    <div class="divider"></div>
    <div class="contact">
      <h1 class="agent-name">Gary Whitlock</h1>
      <p class="agent-title">Broker/Owner</p>
      <p class="address">738 West Pinecrest Ave<br>Suite 410/510<br>Fort Lauderdale, FL 33308</p>
      <ul class="reach">
        <li>
          <svg viewBox="0 0 16 16" aria-hidden="true"><path fill="#f4b92a" d="M3.5 1.5l2.5 0 1 3.5-1.7 1.2a8 8 0 0 0 4.5 4.5L11 9l3.5 1v2.5a1.5 1.5 0 0 1-1.5 1.5A11.5 11.5 0 0 1 2 3a1.5 1.5 0 0 1 1.5-1.5z"/></svg>
          <span>954-327-8846</span>
        </li>
        <li>
          <svg viewBox="0 0 16 16" aria-hidden="true"><rect x="1.5" y="3.5" width="13" height="9" fill="#f4b92a"/><path d="M1.5 3.5l6.5 5 6.5-5" fill="none" stroke="#fff" stroke-width="1.2"/></svg>
          <span>garyshomes@quellmail.com</span>
        </li>
        <li>
          <svg viewBox="0 0 16 16" aria-hidden="true"><circle cx="8" cy="8" r="6.5" fill="#f4b92a"/><path d="M1.5 8h13M8 1.5c-3 3.5-3 9.5 0 13M8 1.5c3 3.5 3 9.5 0 13" fill="none" stroke="#fff" stroke-width="1"/></svg>
          <span>DwellTarrowBay.com</span>
        </li>
      </ul>
    </div>
    <div class="gold-band"></div>
  </section>

  <section class="card card-back" aria-label="Card back">
    <div class="brand brand-back">
      <span class="brand-dot"></span>
      <span class="brand-name">Marlowe Crest Realty, Inc.</span>
    </div>
    <div class="portrait" role="img" aria-label="Portrait photo of Gary Whitlock in a blue checked blazer and pink shirt"></div>
  </section>
</main>
</body>
</html>
```